Need a developer to develop and design my virtual employee recruitment solution website.

I need the entire website developed, from the design, the navigation, the contents of the website, etc. I need a professional looking website yet have that modern look. You can suggest the best fonts, color combinations to use. I need the site to be SEO friendly. I also want high quality stock photos to be used on the website. I wanted to achieve a similar website like this https://remotehelperpool.example/.

Target Market(s)

Ecommerce Entrepreneurs, Businessmen, Cartwell and Bazorra Sellers.

Industry/Entity Type

Professional Service

Coding

Coded - Design and coding required

Number of Pages Required

5+ page

Font styles to use
Sans Serif

Requirements
Must have
• I wanted it to have pages like this https://remotehelperpool.example/
Nice to have
• open for any recommendation you can suggest
Should not have
• Cannot think of any. You can suggest your own here

```html
<!DOCTYPE html>
<html lang="en">
<head>
<meta charset="utf-8">
<title>Brightdesk – Virtual Employee Recruitment Services</title>
<link href="https://fonts.googleapis.com/css2?family=Montserrat:wght@500;600;700&family=Open+Sans:wght@400;600&display=swap" rel="stylesheet">
<style>
:root{
  --blue:#1a63c8;
  --blue-deep:#0f4fa8;
  --navy:#0b2c5c;
  --orange:#f47b20;
  --ink:#1d1d1d;
  --grey:#555;
  --soft:#e6e6e6;
  --white:#fff;
}
*{margin:0;padding:0;box-sizing:border-box}
html,body{width:1200px;height:3432px;overflow:hidden}
body{font-family:"Open Sans",Arial,sans-serif;color:var(--ink);background:var(--white);position:relative}
.abs{position:absolute}
h1,h2,h3,h4,.brand,.nav a{font-family:"Montserrat",Arial,sans-serif}

/* hero */
.hero{left:0;top:0;width:1200px;height:670px;background:linear-gradient(180deg,#2b2f33 0%,#6e7f8a 28%,#a9b2b5 48%,#cfc3b1 70%,#b9a88f 100%)}
.hero-photo{left:640px;top:240px;width:540px;height:400px;border-radius:40% 40% 10% 10%;background:linear-gradient(160deg,rgba(60,50,45,.35),rgba(120,70,40,.35))}
.brand{left:82px;top:48px;color:var(--white);font-weight:700;font-size:28px;letter-spacing:.5px}
.contact-top{top:42px;color:var(--white);font-family:"Montserrat",sans-serif;font-size:18px;display:flex;align-items:center;gap:10px;font-weight:500}
.contact-top.phone{left:590px;font-weight:600}
.contact-top.mail{left:815px}
.arrow{top:305px}
.hero-title{left:100px;top:315px;width:670px;text-align:center;color:var(--white);font-weight:500;font-size:46px;line-height:60px;letter-spacing:.5px}
.btn{left:348px;top:449px;width:183px;height:57px;background:var(--orange);color:var(--white);font-family:"Montserrat",sans-serif;font-weight:700;font-size:16px;display:flex;align-items:center;justify-content:center;letter-spacing:.5px}

/* nav */
.nav{left:0;top:670px;width:1200px;height:65px;background:var(--blue);display:flex;padding-left:82px}
.nav a{color:var(--white);text-decoration:none;font-weight:600;font-size:16px;display:flex;align-items:center;padding:0 25px}
.nav a.active{background:var(--blue-deep);padding:0 30px}

/* intro */
.intro-lead{left:100px;top:808px;width:1000px;text-align:center;color:var(--blue);font-weight:700;font-size:22px;line-height:38px}
.intro-text{left:100px;top:900px;width:1000px;text-align:center;color:var(--grey);font-size:20px;line-height:38px}
.illus{left:170px;top:1060px;width:380px;height:340px;border-radius:45%;background:radial-gradient(circle at 50% 45%,#f4c94a 0 18%,#c9d3f3 19% 55%,#fff 70%)}
.perks{left:616px;top:1115px;width:500px}
.perks h2{color:var(--blue);font-size:27px;font-weight:700;margin-bottom:18px}
.perks li{list-style:none;display:flex;gap:18px;font-size:17.5px;color:var(--ink);line-height:30px;margin-bottom:10px}
.perks li svg{flex:none;margin-top:6px}

/* who */
.who{left:0;top:1502px;width:1200px;height:558px;background:linear-gradient(90deg,#0c3f8e 0%,#114da6 45%,#0b2f6a 100%)}
.who-ring{left:650px;top:1490px;width:560px;height:560px;border-radius:50%;border:18px solid var(--blue);border-right-color:#1e1e1e;border-top-color:#1e1e1e}
.who-photo{left:695px;top:1535px;width:470px;height:470px;border-radius:50%;background:linear-gradient(150deg,#c7a37d,#7b5a43 60%,#3e3a38)}
.who-text{left:117px;top:1588px;width:510px;color:var(--white)}
.who-text h2{font-size:28px;font-weight:700;line-height:34px;margin-bottom:26px}
.who-text p{font-size:15.5px;line-height:24.5px;margin-bottom:12px}

/* why */
.why{left:0;top:2060px;width:1200px;height:948px;background:var(--soft)}
.why-title{left:0;top:2124px;width:1200px;text-align:center;font-size:27px;font-weight:700;color:#222}
.card{width:250px;height:235px;background:var(--white);border:2px solid #d8d8d8;padding:24px 26px}
.card.featured{background:var(--navy);color:var(--white);border-color:var(--navy)}
.card svg{display:block;margin-bottom:18px}
.card h3{font-size:13.5px;font-weight:700;line-height:22px;margin-bottom:10px;letter-spacing:.1px}
.card p{font-size:12.5px;line-height:19px;color:#666}
.card.featured p{color:#dbe4f2}

/* footer */
.footer{left:0;top:3008px;width:1200px;height:424px;background:var(--blue);color:var(--white)}
.f-col{top:3085px}
.f-col h4{font-size:23px;font-weight:500;margin-bottom:34px;position:relative}
.f-col h4::after{content:"";position:absolute;left:0;bottom:-12px;width:36px;height:2px;background:var(--white)}
.f-col p,.f-col a{display:block;color:var(--white);text-decoration:none;font-size:15.5px;line-height:29px}
.socials{display:flex;gap:7px}
.socials span{width:41px;height:41px;border:2px solid var(--white);border-radius:50%}
.f-rule{left:150px;top:3365px;width:900px;height:1px;background:rgba(255,255,255,.35)}
.copy{left:0;top:3378px;width:1200px;text-align:center;font-size:13.5px}
</style>
</head>
<body>

<header>
  <div class="abs hero" role="img" aria-label="Beach scene photo with a man working on a laptop in a deck chair"></div>
  <div class="abs hero-photo" role="img" aria-label="Remote worker relaxing on the sand with a laptop"></div>
  <div class="abs brand">BRIGHTDESK</div>
  <div class="abs contact-top phone">
    <svg width="26" height="26" viewBox="0 0 24 24" fill="none" stroke="#fff" stroke-width="2"><path d="M5 3h4l2 5-3 2a11 11 0 0 0 6 6l2-3 5 2v4a2 2 0 0 1-2 2A17 17 0 0 1 3 5a2 2 0 0 1 2-2z"/></svg>
    (555) 014 2252
  </div>
  <div class="abs contact-top mail">
    <svg width="30" height="22" viewBox="0 0 30 22"><rect width="30" height="22" fill="#fff"/><path d="M0 0l15 11L30 0" fill="none" stroke="#888" stroke-width="2"/></svg>
    hello@brightdesk.example
  </div>
  <svg class="abs arrow" style="left:45px" width="26" height="50" viewBox="0 0 26 50"><path d="M22 5L5 25l17 20" fill="none" stroke="#fff" stroke-width="5"/></svg>
  <svg class="abs arrow" style="left:1145px" width="26" height="50" viewBox="0 0 26 50"><path d="M4 5l17 20L4 45" fill="none" stroke="#fff" stroke-width="5"/></svg>
  <h1 class="abs hero-title">VIRTUAL EMPLOYEE<br>RECRUITMENT SERVICES</h1>
  <a class="abs btn">LEARN MORE</a>
  <nav class="abs nav">
    <a class="active">Home</a><a>About Us</a><a>Services offered</a><a>Pricing</a><a>Testimonials</a><a>FAQs</a><a>Contact Us</a><a>Blog</a>
  </nav>
</header>

<section>
  <p class="abs intro-lead">Tired of being stuck in your 9-5 cubicle job? Exhausted from commuting to and from the office? Want to spend more time with your family? We’ve got you covered.</p>
  <p class="abs intro-text">Brightdesk is a virtual staffing company that helps freelancers and virtual assistants find their perfect work-from-home job. We have a pool of clients from all over the world who are all looking for talented virtual assistants.</p>
  <div class="abs illus" role="img" aria-label="Illustration of a woman working on a laptop with a light bulb and leaves"></div>
  <div class="abs perks">
    <h2>With Brightdesk, you get to:</h2>
    <ul>
      <li><svg width="14" height="14" viewBox="0 0 14 14"><circle cx="7" cy="7" r="7" fill="#1a63c8"/><path d="M5.5 4l3 3-3 3" stroke="#fff" stroke-width="1.8" fill="none"/></svg>Work from the comfort of your home</li>
      <li><svg width="14" height="14" viewBox="0 0 14 14"><circle cx="7" cy="7" r="7" fill="#1a63c8"/><path d="M5.5 4l3 3-3 3" stroke="#fff" stroke-width="1.8" fill="none"/></svg>Have a competitive and steady income</li>
      <li><svg width="14" height="14" viewBox="0 0 14 14"><circle cx="7" cy="7" r="7" fill="#1a63c8"/><path d="M5.5 4l3 3-3 3" stroke="#fff" stroke-width="1.8" fill="none"/></svg>Achieve work-life balance</li>
      <li><svg width="14" height="14" viewBox="0 0 14 14"><circle cx="7" cy="7" r="7" fill="#1a63c8"/><path d="M5.5 4l3 3-3 3" stroke="#fff" stroke-width="1.8" fill="none"/></svg>Learn new skills for free</li>
      <li><svg width="14" height="14" viewBox="0 0 14 14"><circle cx="7" cy="7" r="7" fill="#1a63c8"/><path d="M5.5 4l3 3-3 3" stroke="#fff" stroke-width="1.8" fill="none"/></svg>Work with a dedicated team who can provide you with HR, payroll, IT, and training assistance 24/7!</li>
    </ul>
  </div>
</section>

<section>
  <div class="abs who"></div>
  <div class="abs who-ring"></div>
  <div class="abs who-photo" role="img" aria-label="Person on a video call with colleagues on a laptop"></div>
  <div class="abs who-text">
    <h2>WHO ARE OUR<br>VIRTUAL ASSISTANTS?</h2>
    <p>We have VAs from all over the Philippines.</p>
    <p>Our VA pool is composed of highly dedicated people armed with the right set of skills clients are looking for in a virtual assistant. We hire VAs of varying work experience and skill levels, and we help our VAs improve their skills so that they can get the jobs and clients they want.</p>
    <p>Brightdesk accepts VAs in a variety of niches. Currently, our VAs belongs to one or more of the following groups: Administrative VAs, eCommerce VAs, and Specialist VAs.</p>
    <p>Are you ready to join the team? To start the application process, please click on the button below.</p>
  </div>
</section>

<section>
  <div class="abs why"></div>
  <h2 class="abs why-title">WHY WORK FOR BRIGHTDESK?</h2>

  <div class="abs card" style="left:80px;top:2205px">
    <svg width="56" height="50" viewBox="0 0 56 50" fill="none" stroke="#1a63c8" stroke-width="2"><path d="M4 30h10v16H4zM14 34h12l8-4 14 2-2 6-20 6"/><text x="26" y="20" fill="#1a63c8" stroke="none" font-size="20" font-family="Arial">$</text></svg>
    <h3>COMPETITIVE<br>HOURLY RATES</h3>
    <p>We offer competitive rates based on your years of experience and skill proficiency.</p>
  </div>
  <div class="abs card featured" style="left:344px;top:2205px">
    <svg width="48" height="48" viewBox="0 0 48 48" fill="none" stroke="#fff" stroke-width="2"><circle cx="24" cy="24" r="20"/><circle cx="24" cy="24" r="14"/><path d="M24 14v10l6 4"/></svg>
    <h3>FLEXIBLE HOURS</h3>
    <p>Full-time or part-time? We’ll match you with a client whose staffing needs perfectly matches your availability!</p>
  </div>
  <div class="abs card" style="left:611px;top:2205px">
    <svg width="56" height="54" viewBox="0 0 56 54" fill="none" stroke="#1a63c8" stroke-width="2"><rect x="3" y="6" width="40" height="34"/><path d="M3 16h40M10 22h6v5h-6zM20 22h6v5h-6zM30 22h6v5h-6z"/><circle cx="42" cy="40" r="10" fill="#fff"/><path d="M42 34v6h5"/></svg>
    <h3>FLEXIBLE SCHEDULE</h3>
    <p>We have clients from different time zones all over the world. We’ll help you find the best fit for your schedule.</p>
  </div>
  <div class="abs card" style="left:869px;top:2205px">
    <svg width="48" height="48" viewBox="0 0 48 48" fill="none" stroke="#1a63c8" stroke-width="2"><rect x="6" y="6" width="36" height="36" rx="4"/></svg>
    <h3>WEEKLY PAYOUT<br>VIA PAYVINE</h3>
    <p>Your work is billed by the hour, and we will pay your client-verified hours each week.</p>
  </div>

  <div class="abs card" style="left:80px;top:2455px">
    <svg width="58" height="54" viewBox="0 0 58 54" fill="none" stroke="#1a63c8" stroke-width="2"><rect x="3" y="12" width="42" height="30"/><path d="M16 42v6h16v-6M10 26h14v8H10z"/><circle cx="44" cy="12" r="9" fill="#fff"/><text x="40" y="17" fill="#1a63c8" stroke="none" font-size="13" font-family="Arial">$</text></svg>
    <h3>PAYVINE FEES COVERED</h3>
    <p>Here at AroundClockVA, we shoulder the Payvine fees. We want you to get your hard-earned money in full!</p>
  </div>
  <div class="abs card" style="left:344px;top:2455px">
    <svg width="56" height="50" viewBox="0 0 56 50" fill="none" stroke="#1a63c8" stroke-width="2"><circle cx="28" cy="12" r="9"/><path d="M4 34l24-8 24 8-24 8zM14 38v8h28v-8"/></svg>
    <h3>FREE TRAINING &amp;<br>UPSKILLING</h3>
    <p>Our trainers have created training programs that will help you improve your skills for free.</p>
  </div>
  <div class="abs card" style="left:607px;top:2455px">
    <svg width="56" height="54" viewBox="0 0 56 54" fill="none" stroke="#1a63c8" stroke-width="2"><path d="M4 4h26l8 8v24H4z"/><path d="M10 14h16M10 20h20M10 26h12"/><rect x="16" y="32" width="34" height="16" fill="#fff"/><circle cx="33" cy="40" r="4"/></svg>
    <h3>NO PLACEMENT OR<br>PROCESSING FEE</h3>
    <p>We don’t ask for placement or processing fees. We’re happy to match you with clients for free.</p>
  </div>
  <div class="abs card" style="left:870px;top:2455px">
    <svg width="54" height="54" viewBox="0 0 54 54" fill="none" stroke="#1a63c8" stroke-width="2"><path d="M4 26L27 4l23 22M10 20v28h34V20"/><rect x="21" y="30" width="12" height="18"/></svg>
    <h3>WORK FROM HOME</h3>
    <p>We spare you the time, effort and expense of the daily commute. All the work we offer is home-based.</p>
  </div>

  <div class="abs card" style="left:204px;top:2710px">
    <svg width="48" height="56" viewBox="0 0 48 56" fill="none" stroke="#1a63c8" stroke-width="2"><rect x="6" y="3" width="36" height="50" rx="3"/><rect x="12" y="10" width="24" height="14"/><path d="M12 30h24M12 36h24M12 42h16"/></svg>
    <h3>PAYROLL PROCESSING</h3>
    <p>We want you to focus on doing your client’s tasks, so our Accounting Department will take care of the invoicing for you!</p>
  </div>
  <div class="abs card" style="left:467px;top:2710px">
    <svg width="56" height="56" viewBox="0 0 56 56" fill="none" stroke="#1a63c8" stroke-width="2"><path d="M28 4l4 8 8 1-6 6 2 8-8-4-8 4 2-8-6-6 8-1z"/><path d="M4 40h16v14H4zM20 34h16v20H20zM36 44h16v10H36z"/></svg>
    <h3>VARIOUS POSITIONS<br>AVAILABLE</h3>
    <p>From eCommerce work to content writing, we have a wide range of positions available for you.</p>
  </div>
  <div class="abs card" style="left:729px;top:2710px">
    <svg width="56" height="52" viewBox="0 0 56 52" fill="none" stroke="#1a63c8" stroke-width="2"><path d="M4 8h48v38H4zM28 8v38M10 16h12M10 22h12M34 16h12M34 22h12"/><circle cx="28" cy="8" r="6" fill="#fff"/></svg>
    <h3>CONTINUOUS<br>RE-ASSIGNMENT<br>TO CLIENTS</h3>
    <p>Feel secure that we’re always ready to match you with our steady roster of clients looking for VAs!</p>
  </div>
</section>

<footer>
  <div class="abs footer"></div>
  <div class="abs f-col" style="left:150px">
    <h4>CONTACT US</h4>
    <p>48 Harbor Lane #4B</p>
    <p>Austin 78701 TX</p>
    <p>(555) 014 2252</p>
    <p>hello@brightdesk.example</p>
  </div>
  <div class="abs f-col" style="left:459px">
    <h4>COMPANY</h4>
    <a>Home</a><a>About Us</a><a>Services offered</a><a>Pricing</a><a>Testimonials</a>
  </div>
  <div class="abs f-col" style="left:653px;top:3148px">
    <a>FAQs</a><a>Contact Us</a><a>Blog</a>
  </div>
  <div class="abs f-col" style="left:828px">
    <h4>FOLLOW US</h4>
    <div class="socials" aria-label="Social profiles"><span></span><span></span><span></span><span></span></div>
  </div>
  <div class="abs f-rule"></div>
  <p class="abs copy">© 2020 Brightdesk | All Rights Reserved</p>
</footer>

</body>
</html>
```